Beacon Advisory Website

I currently have a website www.beaconadvisoryinc.com. We are a IT Consulting Company. Our website will pretty much tell out our services. I am looking to enhance my website and make it look more professional. Looking for very classy and Contemporary look and design for my website.

It Company

```html
<!DOCTYPE html>
<html lang="en">
<head>
<meta charset="utf-8">
<title>Beacon Advisory – IT Consulting</title>
<link href="https://fonts.googleapis.com/css2?family=Bebas+Neue&family=Open+Sans:wght@400;600&family=Roboto+Condensed:wght@400;700&display=swap" rel="stylesheet">
<style>
  :root{
    --navy:#0b3a8a;
    --blue:#0a84c6;
    --sky:#16a6e0;
    --ink:#444;
    --muted:#555;
    --light:#f4f4f4;
    --footer:#2b2b2b;
    --footer-base:#202020;
    --white:#fff;
  }
  *{box-sizing:border-box;margin:0;padding:0}
  html,body{width:1200px;height:2748px;overflow:hidden;background:var(--white)}
  body{position:relative;font-family:"Open Sans",Arial,sans-serif;color:var(--ink)}
  .abs{position:absolute}
  .cond{font-family:"Roboto Condensed","Arial Narrow",sans-serif}

  /* header */
  .site-header{left:0;top:0;width:1200px;height:120px;background:var(--white)}
  .brand{left:82px;top:38px;display:flex;align-items:center;gap:14px}
  .brand-mark{width:40px;height:40px;background:var(--blue)}
  .brand-name{font-family:"Roboto Condensed",sans-serif;font-weight:700;font-size:30px;color:var(--navy)}
  .main-nav{left:408px;top:40px;display:flex;height:52px;align-items:center}
  .main-nav a{font-family:"Roboto Condensed",sans-serif;font-size:19px;color:#333;text-decoration:none;padding:0 20px;height:52px;line-height:52px}
  .main-nav a.active{background:var(--navy);color:var(--white)}

  /* hero */
  .hero{left:0;top:120px;width:1200px;height:521px;background:linear-gradient(120deg,#2a5fb0 0%,#3d79c6 40%,#1f55a8 75%,#0d3f8f 100%)}
  .hero-title{left:0;top:262px;width:1200px;text-align:center;font-family:"Bebas Neue",sans-serif;font-size:70px;color:var(--white);letter-spacing:.5px}
  .hero-call{left:0;top:380px;width:1200px;display:flex;justify-content:center;align-items:center;gap:18px;color:var(--white);font-family:"Roboto Condensed",sans-serif;font-size:32px}
  .hero-call b{font-weight:700}
  .phone-ring{width:62px;height:62px;border:2px solid var(--white);border-radius:50%;display:flex;align-items:center;justify-content:center}
  .btn{display:block;text-align:center;font-family:"Roboto Condensed",sans-serif;color:var(--white);text-decoration:none}
  .hero-btn{left:506px;top:473px;width:188px;height:62px;line-height:62px;background:var(--sky);font-size:25px;border-radius:3px}

  /* welcome */
  .welcome-title{left:0;top:693px;width:1200px;text-align:center;font-family:"Roboto Condensed",sans-serif;font-size:44px;color:#444}
  .welcome-title span{color:var(--blue)}
  .welcome-text{left:190px;top:762px;width:820px;text-align:center;font-size:15.5px;line-height:25px;color:var(--muted)}
  .read-btn{left:517px;top:861px;width:166px;height:50px;line-height:50px;background:var(--blue);font-size:21px}

  /* services */
  .services{left:0;top:966px;width:1200px;height:469px;background:linear-gradient(110deg,#1aa0e0 0%,#1b8fd4 45%,#1a6fba 100%)}
  .services-visual{left:73px;top:1020px;width:257px;height:415px;background:linear-gradient(180deg,rgba(255,255,255,.15),rgba(240,200,180,.35));}
  .services-title{left:330px;top:1006px;font-family:"Roboto Condensed",sans-serif;font-size:42px;color:var(--white)}
  .service{width:260px;text-align:center;color:var(--white)}
  .service-icon{width:114px;height:114px;border-radius:50%;background:var(--navy);margin:0 auto;display:flex;align-items:center;justify-content:center}
  .service h3{font-family:"Roboto Condensed",sans-serif;font-weight:700;font-size:23px;margin-top:22px}
  .service p{font-size:15px;line-height:25px;margin-top:10px}
  .viewall-btn{left:326px;top:1330px;width:167px;height:50px;line-height:50px;background:var(--navy);font-size:21px}

  /* solutions */
  .solutions-title{left:0;top:1480px;width:1200px;text-align:center;font-family:"Roboto Condensed",sans-serif;font-size:42px;color:#444}
  .solutions-title span{color:var(--blue)}
  .solution{width:313px;text-align:center}
  .solution-img{width:313px;height:156px}
  .solution h3{font-family:"Roboto Condensed",sans-serif;font-weight:400;font-size:24px;color:var(--blue);margin-top:14px}
  .solution p{font-size:15px;line-height:25px;color:var(--muted);margin-top:6px}

  /* process band */
  .process-band{left:0;top:1896px;width:1200px;height:260px;background:linear-gradient(110deg,#2a9fd6 0%,#1c86c4 55%,#0f6aaa 100%)}
  .feature{display:flex;gap:13px;color:var(--white)}
  .feature-img{width:209px;height:136px;flex:none}
  .feature h3{font-family:"Roboto Condensed",sans-serif;font-weight:400;font-size:30px;margin-top:6px}
  .feature p{font-size:15px;line-height:25px;margin-top:10px;width:230px}

  /* newsletter */
  .news-title{left:0;top:2180px;width:1200px;text-align:center;font-family:"Roboto Condensed",sans-serif;font-size:44px;color:#333}
  .news-text{left:180px;top:2242px;width:840px;text-align:center;font-size:15.5px;line-height:27px;color:var(--muted)}
  .field{height:42px;border:1px solid #ccc;background:var(--light);font-size:15px;color:#666;padding:0 10px;line-height:40px}
  .sub-btn{left:850px;top:2305px;width:167px;height:42px;line-height:42px;background:var(--blue);font-size:22px}

  /* footer */
  .footer{left:0;top:2400px;width:1200px;height:302px;background:var(--footer);color:#ddd}
  .footer h4{font-family:"Roboto Condensed",sans-serif;font-weight:400;font-size:23px;color:var(--blue)}
  .links{list-style:none;margin-top:16px}
  .links li{font-size:15px;height:31px;line-height:31px;display:flex;align-items:center;gap:8px}
  .links li.active{color:var(--blue)}
  .quote{margin-top:14px}
  .testimonial p{font-size:15px;line-height:27px;margin-top:12px;width:320px}
  .client{font-size:15px;font-weight:600;color:var(--blue);margin-top:18px}
  .view-link{font-size:15px;font-weight:600;color:var(--white);text-decoration:underline;margin-top:4px;display:block}
  .contact-row{display:flex;gap:14px;font-size:15px;line-height:25px;margin-top:16px}
  .contact-row svg{flex:none;margin-top:4px}
  .socials{display:flex;gap:24px;margin-top:22px}
  .social{width:48px;height:48px;border-radius:50%;background:#111}
  .social.primary{background:var(--blue)}
  .copyright{left:0;top:2702px;width:1200px;height:46px;background:var(--footer-base);text-align:center;line-height:46px;font-size:15px;color:#ddd}
  .copyright span{color:var(--blue);font-weight:600}
</style>
</head>
<body>

<header class="site-header abs">
  <div class="brand abs"><div class="brand-mark"></div><div class="brand-name">Beacon Advisory</div></div>
  <nav class="main-nav abs">
    <a class="active">HOME</a><a>ABOUT</a><a>SERVICES</a><a>SOLUTION</a><a>RESOURCES</a><a>CAREER</a><a>CONTACT</a>
  </nav>
</header>

<section class="hero abs" role="img" aria-label="Business team smiling around a meeting table, tinted blue"></section>
<h1 class="hero-title abs">DELIVERING EXCEPTIONAL CLIENT SERVICE</h1>
<div class="hero-call abs">
  <span>CALL US ON</span>
  <span class="phone-ring"><svg width="30" height="30" viewBox="0 0 24 24"><path fill="#fff" d="M6.6 10.8a15.2 15.2 0 0 0 6.6 6.6l2.2-2.2c.3-.3.7-.4 1-.2 1.1.4 2.3.6 3.6.6.6 0 1 .4 1 1V20c0 .6-.4 1-1 1A17 17 0 0 1 3 4c0-.6.4-1 1-1h3.5c.6 0 1 .4 1 1 0 1.3.2 2.5.6 3.6.1.3 0 .7-.2 1z"/></svg></span>
  <b>+1 (555) 014 2870</b>
</div>
<a class="btn hero-btn abs">CONTACT US</a>

<h2 class="welcome-title abs">WELCOME TO <span>BEACON ADVISORY</span></h2>
<p class="welcome-text abs">Today's IT market is a dynamic, fast-paced industry, with ever-increasing demands. Meeting these demands for over 25 years, Beacon Advisory maintains a global presence, aggressively recruiting expertly qualified IT and Management Professionals from around the world.</p>
<a class="btn read-btn abs">READ MORE</a>

<section class="services abs" role="img" aria-label="Blue tinted background of hands at a keyboard"></section>
<div class="services-visual abs" role="img" aria-label="Hand pointing upward with one finger"></div>
<h2 class="services-title abs">SERVICE WE PROVIDE</h2>
<div class="service abs" style="left:315px;top:1066px">
  <div class="service-icon"><svg width="58" height="58" viewBox="0 0 58 58" fill="none" stroke="#fff" stroke-width="5"><circle cx="22" cy="30" r="10" stroke-dasharray="5 3"/><circle cx="22" cy="30" r="3" fill="#fff"/><circle cx="42" cy="18" r="7" stroke-dasharray="4 2.5"/><circle cx="42" cy="42" r="7" stroke-dasharray="4 2.5"/></svg></div>
  <h3>Technology</h3>
  <p>Beacon Advisory Training programs are perfect for individuals to enhance their...</p>
</div>
<div class="service abs" style="left:594px;top:1066px">
  <div class="service-icon"><svg width="50" height="58" viewBox="0 0 50 58" fill="none" stroke="#fff" stroke-width="4"><rect x="10" y="3" width="30" height="52" rx="4"/><circle cx="25" cy="28" r="7" stroke-dasharray="3 2"/><line x1="20" y1="48" x2="30" y2="48"/></svg></div>
  <h3>Application Developement</h3>
  <p>Drawing on our experience in all major industries, we develop solutions that meet...</p>
</div>
<div class="service abs" style="left:876px;top:1066px">
  <div class="service-icon"><svg width="58" height="58" viewBox="0 0 58 58" fill="none" stroke="#fff" stroke-width="3"><circle cx="29" cy="29" r="6" fill="#fff"/><circle cx="29" cy="7" r="4"/><circle cx="50" cy="22" r="4"/><circle cx="44" cy="49" r="4"/><circle cx="14" cy="49" r="4"/><circle cx="8" cy="22" r="4"/><path d="M29 23V11M34 27l12-4M33 34l8 12M25 34l-8 12M24 27l-12-4"/></svg></div>
  <h3>Enterprise Integration</h3>
  <p>As organizations work to achieve and sustain competitive advantage...</p>
</div>
<a class="btn viewall-btn abs">VIEW ALL</a>

<h2 class="solutions-title abs">OUR <span>SOLUTIONS</span></h2>
<div class="solution abs" style="left:77px;top:1561px">
  <div class="solution-img" role="img" aria-label="Presenter at a whiteboard with seated colleagues" style="background:linear-gradient(135deg,#e8ecef,#c9d3da)"></div>
  <h3>Dashboards</h3>
  <p>Dashboards are a key component of every organization's Performance Management and Business...</p>
</div>
<div class="solution abs" style="left:443px;top:1561px">
  <div class="solution-img" role="img" aria-label="Businessman touching a glowing data chart" style="background:linear-gradient(135deg,#0c1e3a,#2c5b8c 60%,#0f2747)"></div>
  <h3>Data Warehousing</h3>
  <p>A data warehouse is the concept of data extracted from operational systems and made available...</p>
</div>
<div class="solution abs" style="left:810px;top:1561px">
  <div class="solution-img" role="img" aria-label="Overhead view of a team around a meeting table" style="background:linear-gradient(135deg,#d7dcdf,#a9b6bd)"></div>
  <h3>Business Process Management</h3>
  <p>Beacon Advisory having Process Certified Consultants in to provide Business Process Management...</p>
</div>

<section class="process-band abs" role="img" aria-label="Blue tinted background of business handshake"></section>
<div class="feature abs" style="left:77px;top:1949px">
  <div class="feature-img" role="img" aria-label="Three colleagues working at a laptop" style="background:linear-gradient(135deg,#eef3f6,#b8cbd8)"></div>
  <div><h3>Our Processs</h3><p>We bring together seasoned IT executives and battle-tested computer support personnel...</p></div>
</div>
<div class="feature abs" style="left:637px;top:1949px">
  <div class="feature-img" role="img" aria-label="Overhead view of a team meeting" style="background:linear-gradient(135deg,#dfe4e6,#9fb0b9)"></div>
  <div><h3>Staff Augmentation</h3><p>For years Beacon Advisory has been offering our customers the ability to augment their existing...</p></div>
</div>

<h2 class="news-title abs">Newsletter</h2>
<p class="news-text abs">Lorem Ipsum is simply dummy text of the printing and typesetting industry. Lorem Ipsum has been the industry's standard dummy text ever since the 1500.</p>
<div class="field abs" style="left:183px;top:2305px;width:312px">Enter Name</div>
<div class="field abs" style="left:518px;top:2305px;width:310px">Enter Email</div>
<a class="btn sub-btn abs">SUBSCRIBE</a>

<footer class="footer abs">
  <div class="abs" style="left:77px;top:28px">
    <h4>Useful Links</h4>
    <ul class="links">
      <li class="active"><svg width="16" height="10" viewBox="0 0 16 10"><path d="M0 5h14M10 1l4 4-4 4" stroke="#0a84c6" stroke-width="1.6" fill="none"/></svg>Home</li>
      <li><svg width="16" height="10" viewBox="0 0 16 10"><path d="M0 5h14M10 1l4 4-4 4" stroke="#fff" stroke-width="1.6" fill="none"/></svg>About</li>
      <li><svg width="16" height="10" viewBox="0 0 16 10"><path d="M0 5h14M10 1l4 4-4 4" stroke="#fff" stroke-width="1.6" fill="none"/></svg>Services</li>
      <li><svg width="16" height="10" viewBox="0 0 16 10"><path d="M0 5h14M10 1l4 4-4 4" stroke="#fff" stroke-width="1.6" fill="none"/></svg>Solution</li>
      <li><svg width="16" height="10" viewBox="0 0 16 10"><path d="M0 5h14M10 1l4 4-4 4" stroke="#fff" stroke-width="1.6" fill="none"/></svg>Resources</li>
      <li><svg width="16" height="10" viewBox="0 0 16 10"><path d="M0 5h14M10 1l4 4-4 4" stroke="#fff" stroke-width="1.6" fill="none"/></svg>Career</li>
      <li><svg width="16" height="10" viewBox="0 0 16 10"><path d="M0 5h14M10 1l4 4-4 4" stroke="#fff" stroke-width="1.6" fill="none"/></svg>Contact</li>
    </ul>
  </div>
  <div class="testimonial abs" style="left:445px;top:28px">
    <h4>Testimonial</h4>
    <svg class="quote" width="30" height="24" viewBox="0 0 30 24"><path fill="#0a84c6" d="M0 12C0 5 4 1 11 0v5c-3 1-5 3-5 6h5v13H0zM17 12c0-7 4-11 11-12v5c-3 1-5 3-5 6h5v13H17z"/></svg>
    <p>Lorem Ipsum is simply dummy text of the printing and typesetting industry. Lorem Ipsum has been the industry.</p>
    <div class="client">- Client Name</div>
    <a class="view-link">VIEW ALL</a>
  </div>
  <div class="abs" style="left:810px;top:28px">
    <h4>Get In Touch</h4>
    <div class="contact-row" style="margin-top:22px"><svg width="14" height="20" viewBox="0 0 14 20"><path fill="#0a84c6" d="M7 0a7 7 0 0 0-7 7c0 5 7 13 7 13s7-8 7-13a7 7 0 0 0-7-7zm0 10a3 3 0 1 1 0-6 3 3 0 0 1 0 6z"/></svg><span>240 Harbor Lane, Suite 310<br>Westfield, NJ 07000</span></div>
    <div class="contact-row"><svg width="18" height="18" viewBox="0 0 24 24"><path fill="#0a84c6" d="M6.6 10.8a15.2 15.2 0 0 0 6.6 6.6l2.2-2.2c.3-.3.7-.4 1-.2 1.1.4 2.3.6 3.6.6.6 0 1 .4 1 1V20c0 .6-.4 1-1 1A17 17 0 0 1 3 4c0-.6.4-1 1-1h3.5c.6 0 1 .4 1 1 0 1.3.2 2.5.6 3.6.1.3 0 .7-.2 1z"/></svg><span>+1 (555) 014 2870</span></div>
    <div class="contact-row"><svg width="18" height="14" viewBox="0 0 18 14"><rect x="1" y="1" width="16" height="12" fill="none" stroke="#0a84c6" stroke-width="1.6"/><path d="M1 1l8 7 8-7" fill="none" stroke="#0a84c6" stroke-width="1.6"/></svg><span>info@beaconadvisory.com</span></div>
    <div class="socials">
      <span class="social primary" aria-label="Social profile"></span>
      <span class="social" aria-label="Social profile"></span>
      <span class="social" aria-label="Social profile"></span>
    </div>
  </div>
</footer>
<div class="copyright abs">© <span>Beacon Advisory Inc</span> - 2016. All Rights Reserved.</div>

</body>
</html>
```